LHP Regal Business Card Design 2020

Your Manor Steward is looking for a business card that is clean and straight to the point but still looks high-end and attractive. We are a team comprised of management and field professionals focused on the high-end residential marketplace. We serve homeowners and trade professionals directly based out of the Metrowest/Boston area. We provide client services as well as construction/renovation services.
We are aiming for a black and white feel (white background and black text) and a matte finish with rounded edges.

We want to emphasis our vision of "Homes - Renovations - Relations".
Dana Pellham is the president of LHP

Please include the following areas we service: Boston/Cape/Newport
Please make sure to include Dana's mobile (555) 213 4480 & office number (555) 640 1937, email dana@yourmanorsteward.example and website www.yourmanorsteward.example

Colors

Designer to choose only greyscale colors for use in the design.

Requirements
Must have
• Include "Homes - Renovations - Relations" in design

Include "After Hours Emergency Support # 1800 555 0142" with icon

```html
<!DOCTYPE html>
<html lang="en">
<head>
<meta charset="utf-8">
<title>LHP Business Cards</title>
<link href="https://fonts.googleapis.com/css2?family=Montserrat:wght@700;800&family=Open+Sans:wght@400;600&display=swap" rel="stylesheet">
<style>
:root{
  --bg:#e2e2e2;
  --card:#f4f4f4;
  --ink:#2b2b2b;
  --ink-soft:#3a3a3a;
  --band:#2b2b2b;
  --band-end:#5e5e5e;
  --rule:#3a3a3a;
  --back-mark:#4a4a4a;
  --back-text:#dcdcdc;
}
*{margin:0;padding:0;box-sizing:border-box}
html,body{width:1063px;height:1200px;overflow:hidden}
body{background:radial-gradient(ellipse at center,#ededed 0%,var(--bg) 100%);font-family:"Open Sans",Arial,sans-serif;color:var(--ink);position:relative}
.card{position:absolute;width:384px;height:220px;border-radius:12px;background:var(--card);overflow:hidden;box-shadow:2px 4px 8px rgba(0,0,0,.35)}
.col-a{left:127px}.col-b{left:559px}
.row-1{top:106px}.row-2{top:359px}.row-3{top:617px}.row-4{top:873px}

.card-back{background:var(--band)}
.back-mark{position:absolute;left:0;right:0;top:52px;text-align:center;font-family:"Montserrat",sans-serif;font-weight:800;font-size:82px;letter-spacing:2px;color:var(--back-mark);line-height:1}
.back-tagline{position:absolute;left:0;right:0;top:189px;text-align:center;font-size:9.5px;letter-spacing:1.6px;color:var(--back-text)}

.brand{position:absolute;left:24px;top:24px}
.brand-name{font-family:"Montserrat",sans-serif;font-weight:800;font-size:46px;line-height:1;color:var(--ink);letter-spacing:1px}
.brand-sub{font-family:"Montserrat",sans-serif;font-weight:700;font-size:7.6px;letter-spacing:1px;color:var(--ink);margin-top:6px;padding-left:4px}
.brand-centered{left:0;right:0;top:30px;text-align:center}
.brand-centered .brand-name{font-size:54px}
.brand-centered .brand-sub{font-size:9px;padding-left:0;margin-top:7px}

.person{position:absolute;right:25px;top:94px;text-align:right}
.person-name{font-family:"Montserrat",sans-serif;font-weight:700;font-size:13px;color:var(--ink);text-transform:uppercase}
.person-role{font-size:9.2px;color:var(--ink-soft);margin-top:1px}

.rule{position:absolute;left:24px;right:23px;top:128px;height:1px;background:var(--rule)}

.contacts{position:absolute;left:24px;top:138px;list-style:none}
.contacts li{display:flex;align-items:center;height:12.8px;font-size:9.2px;color:var(--ink)}
.contacts svg{width:8px;height:8px;margin-right:4px;fill:var(--ink)}
.areas{position:absolute;right:25px;top:176px;font-size:9.2px;color:var(--ink);word-spacing:1px}

.band{position:absolute;left:0;right:0;bottom:0;height:21px;background:linear-gradient(90deg,var(--band) 0%,var(--band) 78%,var(--band-end) 100%)}
.band-url{position:absolute;left:24px;top:4px;font-size:9.5px;letter-spacing:1px;color:#e6e6e6}
.band-mark{position:absolute;right:25px;top:1px;font-family:"Montserrat",sans-serif;font-weight:800;font-size:17px;color:#f4f4f4;line-height:20px}
.icons{position:absolute;width:0;height:0}
</style>
</head>
<body>

<svg class="icons" aria-hidden="true">
  <symbol id="i-mobile" viewBox="0 0 10 10"><path d="M2.5 0h5a.8.8 0 0 1 .8.8v8.4a.8.8 0 0 1-.8.8h-5a.8.8 0 0 1-.8-.8V.8A.8.8 0 0 1 2.5 0zm.3 1v7h4.4V1zm2.2 7.4a.5.5 0 1 0 0 1 .5.5 0 0 0 0-1z"/></symbol>
  <symbol id="i-phone" viewBox="0 0 10 10"><path d="M2.2.3 3.6 2c.3.3.2.7 0 1l-.7.7c.6 1.3 1.7 2.4 3 3l.7-.7c.3-.3.7-.3 1 0l1.7 1.3c.3.3.3.7 0 1l-.9.9C7.6 10 4.6 8.6 2.9 6.9S0 2.4.8 1.2l.9-.9c.1-.2.3-.2.5 0z"/></symbol>
  <symbol id="i-alarm" viewBox="0 0 10 10"><path d="M3 4.5a2 2 0 0 1 4 0V8H3zM2 8.3h6V10H2zM4.7 0h.6v1.6h-.6zM1 1.3l.4-.4 1.1 1.1-.4.4zm7.6-.4.4.4-1.1 1.1-.4-.4zM0 4h1.5v.6H0zm8.5 0H10v.6H8.5z"/></symbol>
  <symbol id="i-mail" viewBox="0 0 10 10"><path d="M0 1.8h10v6.4H0zm1 .8v4.8h8V2.6L5 5.3z" fill-rule="evenodd"/></symbol>
</svg>

<section class="card card-back col-a row-1">
  <div class="back-mark">LHP</div>
  <p class="back-tagline">HOMES - RENOVATIONS - RELATIONS</p>
</section>

<section class="card col-b row-1">
  <div class="brand"><div class="brand-name">LHP</div><div class="brand-sub">YOUR MANOR STEWARD</div></div>
  <div class="person"><div class="person-name">Dana Pellham</div><div class="person-role">President</div></div>
  <div class="rule"></div>
  <ul class="contacts">
    <li><svg><use href="#i-mobile"/></svg>(555) 213 4480</li>
    <li><svg><use href="#i-phone"/></svg>(555) 640 1937</li>
    <li><svg><use href="#i-alarm"/></svg>(800) 555 0142</li>
    <li><svg><use href="#i-mail"/></svg>dana@yourmanorsteward.example</li>
  </ul>
  <p class="areas">ASHBY | COVE | HALDEN</p>
  <div class="band"><span class="band-url">yourmanorsteward.example</span><span class="band-mark">LHP</span></div>
</section>

<section class="card col-a row-2">
  <div class="brand"><div class="brand-name">LHP</div><div class="brand-sub">YOUR MANOR STEWARD</div></div>
  <div class="person"><div class="person-name">Owen Marsh</div><div class="person-role">Vice President</div></div>
  <div class="rule"></div>
  <ul class="contacts">
    <li><svg><use href="#i-mobile"/></svg>(555) 213 4480</li>
    <li><svg><use href="#i-phone"/></svg>(555) 640 1937</li>
    <li><svg><use href="#i-alarm"/></svg>(800) 555 0142</li>
    <li><svg><use href="#i-mail"/></svg>dana@yourmanorsteward.example</li>
  </ul>
  <p class="areas">ASHBY | COVE | HALDEN</p>
  <div class="band"><span class="band-url">yourmanorsteward.example</span><span class="band-mark">LHP</span></div>
</section>

<section class="card col-b row-2">
  <div class="brand"><div class="brand-name">LHP</div><div class="brand-sub">YOUR MANOR STEWARD</div></div>
  <div class="person"><div class="person-name">Luca Brenner</div><div class="person-role">Client Services</div></div>
  <div class="rule"></div>
  <ul class="contacts">
    <li><svg><use href="#i-mobile"/></svg>(555) 213 4480</li>
    <li><svg><use href="#i-phone"/></svg>(555) 640 1937</li>
    <li><svg><use href="#i-alarm"/></svg>(800) 555 0142</li>
    <li><svg><use href="#i-mail"/></svg>dana@yourmanorsteward.example</li>
  </ul>
  <p class="areas">ASHBY | COVE | HALDEN</p>
  <div class="band"><span class="band-url">yourmanorsteward.example</span><span class="band-mark">LHP</span></div>
</section>

<section class="card col-a row-3">
  <div class="brand"><div class="brand-name">LHP</div><div class="brand-sub">YOUR MANOR STEWARD</div></div>
  <div class="person"><div class="person-name">Silvia Montero</div><div class="person-role">Client Services</div></div>
  <div class="rule"></div>
  <ul class="contacts">
    <li><svg><use href="#i-mobile"/></svg>(555) 213 4480</li>
    <li><svg><use href="#i-phone"/></svg>(555) 640 1937</li>
    <li><svg><use href="#i-alarm"/></svg>(800) 555 0142</li>
    <li><svg><use href="#i-mail"/></svg>dana@yourmanorsteward.example</li>
  </ul>
  <p class="areas">ASHBY | COVE | HALDEN</p>
  <div class="band"><span class="band-url">yourmanorsteward.example</span><span class="band-mark">LHP</span></div>
</section>

<section class="card col-b row-3">
  <div class="brand"><div class="brand-name">LHP</div><div class="brand-sub">YOUR MANOR STEWARD</div></div>
  <div class="person"><div class="person-name">Paul Kerrigan</div><div class="person-role">Field Service Technician</div></div>
  <div class="rule"></div>
  <ul class="contacts">
    <li><svg><use href="#i-mobile"/></svg>(555) 213 4480</li>
    <li><svg><use href="#i-phone"/></svg>(555) 640 1937</li>
    <li><svg><use href="#i-alarm"/></svg>(800) 555 0142</li>
    <li><svg><use href="#i-mail"/></svg>dana@yourmanorsteward.example</li>
  </ul>
  <p class="areas">ASHBY | COVE | HALDEN</p>
  <div class="band"><span class="band-url">yourmanorsteward.example</span><span class="band-mark">LHP</span></div>
</section>

<section class="card col-a row-4">
  <div class="brand"><div class="brand-name">LHP</div><div class="brand-sub">YOUR MANOR STEWARD</div></div>
  <div class="person"><div class="person-name">Rick Della Vale</div><div class="person-role">Lead Field Service Technician</div></div>
  <div class="rule"></div>
  <ul class="contacts">
    <li><svg><use href="#i-mobile"/></svg>(555) 213 4480</li>
    <li><svg><use href="#i-phone"/></svg>(555) 640 1937</li>
    <li><svg><use href="#i-alarm"/></svg>(800) 555 0142</li>
    <li><svg><use href="#i-mail"/></svg>dana@yourmanorsteward.example</li>
  </ul>
  <p class="areas">ASHBY | COVE | HALDEN</p>
  <div class="band"><span class="band-url">yourmanorsteward.example</span><span class="band-mark">LHP</span></div>
</section>

<section class="card col-b row-4">
  <div class="brand brand-centered"><div class="brand-name">LHP</div><div class="brand-sub">YOUR MANOR STEWARD</div></div>
  <div class="rule"></div>
  <ul class="contacts">
    <li><svg><use href="#i-mobile"/></svg>(555) 213 4480</li>
    <li><svg><use href="#i-phone"/></svg>(555) 640 1937</li>
    <li><svg><use href="#i-alarm"/></svg>(800) 555 0142</li>
    <li><svg><use href="#i-mail"/></svg>dana@yourmanorsteward.example</li>
  </ul>
  <p class="areas">ASHBY | COVE | HALDEN</p>
  <div class="band"><span class="band-url">yourmanorsteward.example</span><span class="band-mark">LHP</span></div>
</section>

</body>
</html>
```